Kor'v Meridell Travel

We need a sleek, professional, inviting card to elicit global travel for the experienced and professional traveler. Royal blue, black and silver. (perhaps the wording could be silver with black shadow?-get creative) Maybe a watermark on the front and the full raised logo on the back.
We want a stylish and modern card, but professional.

```html
<!DOCTYPE html>
<html lang="en">
<head>
<meta charset="UTF-8">
<title>Kor'v Meridell Travel — Business Card</title>
<link href="https://fonts.googleapis.com/css2?family=Montserrat:wght@600;700&family=Open+Sans:ital,wght@0,400;1,400&display=swap" rel="stylesheet">
<style>
  :root {
    --backdrop: #2a2a2c;
    --card: #1c1c1d;
    --card-edge: #0e0e0f;
    --blue: #29a9e1;
    --green: #8dc63f;
    --text: #d9d9d9;
    --muted: #b5b5b5;
    --silver: #8a8a8c;
    --silver-light: #c8c8ca;
  }
  * { box-sizing: border-box; margin: 0; padding: 0; }
  html, body { width: 1200px; height: 900px; overflow: hidden; }
  body {
    background: var(--backdrop);
    display: flex;
    flex-direction: column;
    align-items: center;
    justify-content: center;
    gap: 56px;
    font-family: "Open Sans", Arial, sans-serif;
  }
  .card {
    width: 640px;
    height: 366px;
    background: var(--card);
    box-shadow: 0 18px 40px rgba(0,0,0,.55);
    border-bottom: 2px solid var(--card-edge);
    position: relative;
  }

  /* Front */
  .card-front { display: flex; align-items: center; padding: 0 44px; }
  .brand {
    width: 270px;
    display: flex;
    flex-direction: column;
    align-items: center;
    gap: 10px;
  }
  .brand-mark {
    width: 18px; height: 18px; background: var(--green);
  }
  .brand-name {
    font-family: "Montserrat", Arial, sans-serif;
    font-weight: 700;
    font-size: 23px;
    letter-spacing: .5px;
    color: var(--blue);
    text-align: center;
    line-height: 1.25;
  }
  .brand-rule { width: 230px; height: 2px; background: var(--green); }
  .divider {
    width: 1px; height: 230px; background: var(--blue);
    margin: 0 30px 0 24px;
  }
  .contact { color: var(--text); font-size: 15px; line-height: 1.45; }
  .contact-name {
    font-family: "Montserrat", Arial, sans-serif;
    font-weight: 700;
    font-size: 21px;
    color: var(--blue);
    letter-spacing: .5px;
  }
  .contact-title { font-style: italic; color: var(--muted); margin-bottom: 8px; }
  .contact-address { margin-bottom: 8px; }
  .contact-line { display: flex; align-items: center; gap: 8px; }
  .contact-line svg { width: 13px; height: 13px; flex: none; fill: var(--green); }

  /* Back */
  .card-back {
    display: flex; flex-direction: column; align-items: center; justify-content: center; gap: 14px;
  }
  .back-mark { width: 22px; height: 22px; background: var(--silver); }
  .back-name {
    font-family: "Montserrat", Arial, sans-serif;
    font-weight: 700;
    font-size: 40px;
    letter-spacing: 1.5px;
    color: var(--silver-light);
  }
  .back-rule { width: 420px; height: 2px; background: var(--silver); }
</style>
</head>
<body>

  <section class="card card-front">
    <div class="brand">
      <span class="brand-mark"></span>
      <div class="brand-name">Kor'v Meridell Travel</div>
      <span class="brand-rule"></span>
    </div>
    <span class="divider"></span>
    <div class="contact">
      <div class="contact-name">DANE HOLLOWAY</div>
      <div class="contact-title">President</div>
      <div class="contact-address">1840 Harbor Crest Way<br>Bayview CA 90412</div>
      <div class="contact-line">
        <svg viewBox="0 0 16 16"><path d="M3.5 1.5l2.5 0 1 3.5-1.7 1.2a8 8 0 0 0 4.5 4.5l1.2-1.7 3.5 1v2.5c0 .8-.7 1.5-1.5 1.5C6.6 14 2 9.4 2 3c0-.8.7-1.5 1.5-1.5z"/></svg>
        555-014-2876
      </div>
      <div class="contact-line">
        <svg viewBox="0 0 16 16"><path d="M1 3h14v10H1z M1.5 3.5L8 9l6.5-5.5" fill="none" stroke="#8dc63f" stroke-width="1.6"/></svg>
        info@korvmeridell.com
      </div>
      <div class="contact-line">
        <svg viewBox="0 0 16 16"><circle cx="8" cy="8" r="6.5" fill="none" stroke="#8dc63f" stroke-width="1.6"/><path d="M1.5 8h13M8 1.5c3 3.5 3 9.5 0 13M8 1.5c-3 3.5-3 9.5 0 13" fill="none" stroke="#8dc63f" stroke-width="1.2"/></svg>
        www.korvmeridell.com
      </div>
    </div>
  </section>

  <section class="card card-back">
    <span class="back-mark"></span>
    <div class="back-name">Kor'v Meridell Travel</div>
    <span class="back-rule"></span>
  </section>

</body>
</html>
```